PHD-project

i need the figures to be in the same stile. info is inside the file. There are 5 figures that need redesign. this is for PhD.

Target Market(s)

it will be used in my phd

Colors

```html
<!DOCTYPE html>
<html lang="en">
<head>
<meta charset="utf-8">
<title>Contribution Area Diagrams</title>
<link rel="stylesheet" href="https://fonts.googleapis.com/css2?family=Roboto:wght@700;900&display=swap">
<style>
  :root {
    --ink: #2a2566;
    --accent-red: #ec1c24;
    --ring-orange: #fb9c00;
    --ring-red: #ec1c24;
    --ring-purple: #4a3ace;
    --joint-red: #e01208;
    --joint-dark: #4a0820;
    --disc: #ffffff;
    --page: #ffffff;
  }
  html, body {
    margin: 0;
    padding: 0;
    width: 1200px;
    height: 1200px;
    overflow: hidden;
    background: var(--page);
  }
  .canvas {
    display: block;
    width: 1200px;
    height: 1200px;
  }
  .label {
    font-family: "Roboto", Arial, sans-serif;
    font-weight: 700;
    fill: var(--ink);
    text-anchor: middle;
  }
  .label--accent { fill: var(--accent-red); }
  .label .small { font-size: 0.72em; }
  .chain .label { font-size: 30px; }
  .venn .label { font-size: 40px; }
  .ring { fill: none; stroke-width: 78; }
  .ring--orange { stroke: var(--ring-orange); stroke-linecap: round; }
  .ring--red { stroke: var(--ring-red); }
  .ring--purple { stroke: var(--ring-purple); stroke-linecap: round; }
  .disc { fill: var(--disc); }
  .joint--red { fill: var(--joint-red); }
  .joint--dark { fill: var(--joint-dark); }
</style>
</head>
<body>
<svg class="canvas" viewBox="0 0 1500 1500" xmlns="http://www.w3.org/2000/svg">
  <defs>
    <filter id="disc-shadow" x="-30%" y="-30%" width="160%" height="160%">
      <feDropShadow dx="0" dy="14" stdDeviation="12" flood-color="#000" flood-opacity="0.28"/>
    </filter>
    <linearGradient id="venn-left" x1="0" y1="0" x2="1" y2="0">
      <stop offset="0" stop-color="#5cc6ec"/>
      <stop offset="0.5" stop-color="#55bbe6"/>
      <stop offset="1" stop-color="#2f8ecb"/>
    </linearGradient>
    <linearGradient id="venn-right" x1="0" y1="0" x2="1" y2="0">
      <stop offset="0" stop-color="#b3e3f5"/>
      <stop offset="1" stop-color="#8fbadf"/>
    </linearGradient>
  </defs>

  <!-- Linked rings diagram -->
  <g class="chain">
    <path class="ring ring--orange" d="M179 440 A201 201 0 0 0 581 440"/>
    <path class="ring ring--red" d="M582 440 A201 201 0 0 1 985 440"/>
    <path class="ring ring--purple" d="M986 440 A201 201 0 0 0 1388 440"/>

    <circle class="disc" cx="380" cy="440" r="162" filter="url(#disc-shadow)"/>
    <circle class="disc" cx="783" cy="440" r="162" filter="url(#disc-shadow)"/>
    <circle class="disc" cx="1187" cy="440" r="162" filter="url(#disc-shadow)"/>

    <circle class="joint--red" cx="582" cy="440" r="39"/>
    <circle class="joint--dark" cx="985" cy="440" r="39"/>

    <text class="label">
      <tspan x="380" y="411">DESIGN THINKING</tspan>
      <tspan x="380" y="449"><tspan class="small">IN</tspan> MANAGEMENT</tspan>
      <tspan x="380" y="486"><tspan class="small">AND</tspan> BUSINESS</tspan>
      <tspan x="380" y="523">STRATGEY</tspan>
    </text>
    <text class="label label--accent">
      <tspan x="783" y="439">CONTRIBUTION</tspan>
      <tspan x="783" y="476">AREA</tspan>
    </text>
    <text class="label">
      <tspan x="1185" y="411">RESEARCH</tspan>
      <tspan x="1187" y="449">THROUGH</tspan>
      <tspan x="1187" y="486">DESIGN - RID</tspan>
    </text>
  </g>

  <!-- Overlap diagram -->
  <g class="venn">
    <ellipse cx="1005" cy="1145" rx="410" ry="235" fill="url(#venn-right)"/>
    <ellipse cx="562" cy="1145" rx="410" ry="235" fill="url(#venn-left)" opacity="0.92"/>

    <text class="label">
      <tspan x="416" y="1103">DESIGN THINKING</tspan>
      <tspan x="416" y="1152"><tspan class="small">IN</tspan> MANAGEMENT</tspan>
      <tspan x="416" y="1201"><tspan class="small">AND</tspan> BUSINESS</tspan>
      <tspan x="416" y="1250">STRATGEY</tspan>
    </text>
    <text class="label label--accent">
      <tspan x="774" y="1142">CONTRIBUTION</tspan>
      <tspan x="774" y="1193">AREA</tspan>
    </text>
    <text class="label">
      <tspan x="1150" y="1118">RESEARCH</tspan>
      <tspan x="1155" y="1167">THROUGH</tspan>
      <tspan x="1155" y="1216">DESIGN - RID</tspan>
    </text>
  </g>
</svg>
</body>
</html>
```